Business Card for Professional Photographer

I'm looking for an eye catching modern clean design that compliments my logo/ website fonts & colours.
I specialise in architecture, corporate & commercial photography so I'm marketing to professional clients rather than portrait / wedding clients.

I would prefer to not have a solid black design.

My logo brand guide is as follows :

Main front font. : Reislust
Main font colour : #fff
Slogan front font : Ubuntu Bold
Monogram front font : Venti Medium
Container colour : #fff

I need print ready files in pdf .png & .eps formats.

Included in the files below are some screen grabs as reference to font & colours etc.

```html
<!DOCTYPE html>
<html lang="en">
<head>
<meta charset="utf-8">
<title>Lumen Line – Business Card</title>
<link rel="stylesheet" href="https://fonts.googleapis.com/css2?family=Ubuntu:wght@400;700&family=Roboto:wght@400&family=Saira+Condensed:wght@600&display=swap">
<style>
  :root {
    --backdrop: #b4b4b4;
    --gold-light: #e6dc9a;
    --gold-mid: #d2b56c;
    --gold-deep: #b8914a;
    --gold-text: #b48a3e;
    --ink: #1a1a1a;
    --paper: #f4f4f2;
    --paper-edge: #e9e9e7;
    --text-dark: #2a2a2a;
  }
  * { margin: 0; padding: 0; box-sizing: border-box; }
  html, body { width: 1200px; height: 576px; overflow: hidden; }
  body { background: var(--backdrop); position: relative; font-family: "Roboto", sans-serif; }

  .card {
    position: absolute;
    top: 138px;
    width: 484px;
    height: 294px;
    border-radius: 10px;
    box-shadow: 0 3px 8px rgba(0,0,0,0.25);
  }

  /* Front */
  .card-front {
    left: 82px;
    background: linear-gradient(115deg, var(--gold-deep) 0%, var(--gold-mid) 40%, var(--gold-light) 100%);
  }
  .front-brand {
    position: absolute;
    left: 66px;
    top: 96px;
    display: flex;
    align-items: center;
    gap: 20px;
  }
  .brand-dot {
    width: 74px; height: 74px;
    border: 3px solid var(--ink);
    border-radius: 50%;
  }
  .front-brand .brand-name {
    font-family: "Ubuntu", sans-serif;
    font-weight: 400;
    font-size: 23px;
    letter-spacing: 3px;
    color: var(--ink);
  }
  .front-brand .brand-tagline {
    font-family: "Ubuntu", sans-serif;
    font-weight: 700;
    font-size: 7.5px;
    letter-spacing: 1.6px;
    color: var(--ink);
    margin-top: 3px;
  }
  .front-web {
    position: absolute;
    left: 0; right: 0;
    bottom: 24px;
    text-align: center;
    font-family: "Ubuntu", sans-serif;
    font-size: 13px;
    letter-spacing: 2px;
    color: var(--ink);
  }

  /* Back */
  .card-back {
    left: 602px;
    width: 480px;
    height: 292px;
    background: linear-gradient(180deg, var(--paper) 0%, var(--paper-edge) 100%);
  }
  .back-brand {
    position: absolute;
    left: 36px;
    top: 100px;
    width: 170px;
    text-align: center;
  }
  .back-brand .brand-dot {
    width: 64px; height: 64px;
    border-color: var(--gold-text);
    margin: 0 auto 14px;
  }
  .back-brand .brand-name {
    font-family: "Ubuntu", sans-serif;
    font-size: 16px;
    letter-spacing: 2px;
    color: var(--gold-text);
  }
  .back-brand .brand-tagline {
    font-family: "Ubuntu", sans-serif;
    font-weight: 700;
    font-size: 5.5px;
    letter-spacing: 1.1px;
    color: var(--gold-text);
    margin-top: 2px;
  }
  .divider {
    position: absolute;
    left: 231px;
    top: 66px;
    width: 1px;
    height: 162px;
    background: linear-gradient(180deg, transparent, var(--gold-mid) 20%, var(--gold-mid) 80%, transparent);
  }
  .contact {
    position: absolute;
    left: 267px;
    top: 74px;
    color: var(--text-dark);
  }
  .contact-name {
    font-family: "Saira Condensed", sans-serif;
    font-weight: 600;
    font-size: 19px;
    color: var(--gold-text);
    line-height: 1.1;
  }
  .contact-role { font-size: 12.5px; margin-top: 1px; }
  .contact-list { list-style: none; margin-top: 26px; }
  .contact-list li {
    display: flex; align-items: center; gap: 10px;
    font-size: 12.5px; line-height: 18.5px;
  }
  .contact-list svg { width: 10px; height: 10px; fill: none; stroke: var(--gold-text); stroke-width: 1.4; }
  .contact-address { font-size: 12.5px; margin-top: 6px; }
</style>
</head>
<body>
  <section class="card card-front">
    <div class="front-brand">
      <div class="brand-dot"></div>
      <div>
        <div class="brand-name">LUMEN LINE</div>
        <div class="brand-tagline">Architecture Corporate Commercial</div>
      </div>
    </div>
    <div class="front-web">www.lumenline.com.au</div>
  </section>

  <section class="card card-back">
    <div class="back-brand">
      <div class="brand-dot"></div>
      <div class="brand-name">LUMEN LINE</div>
      <div class="brand-tagline">Architecture Corporate Commercial</div>
    </div>
    <div class="divider"></div>
    <div class="contact">
      <div class="contact-name">Marcus Hale</div>
      <div class="contact-role">Photographer</div>
      <ul class="contact-list">
        <li><svg viewBox="0 0 10 10"><path d="M2 1 L4 1 L4.5 3 L3.4 3.8 Q4.5 6 6.2 6.6 L7 5.5 L9 6 L9 8 Q5 9 1.5 4.5 Q1 2.5 2 1 Z"/></svg>0412555018</li>
        <li><svg viewBox="0 0 10 10"><rect x="0.8" y="2" width="8.4" height="6"/><path d="M0.8 2 L5 5.5 L9.2 2"/></svg>info@lumenline.com.au</li>
        <li><svg viewBox="0 0 10 10"><circle cx="5" cy="5" r="4"/><path d="M1 5 H9 M5 1 Q2.5 5 5 9 M5 1 Q7.5 5 5 9"/></svg>www.lumenline.com.au</li>
      </ul>
      <div class="contact-address">48 Harbour Rd Portland Vic 3305</div>
    </div>
  </section>
</body>
</html>
```